Business Card- Can you make it cool vs boring!

Need a refresh on my business card! Want it to be modern but simple, classic and a pop of coolness! we do senior living and it is boring. but that doesn't mean our business card have to look boring! Open to two sided cards. our website is www.Dunmere-PK.com

Target Market(s)

capital market

Industry/Entity Type

senior housing/ real estate

Contact Information for Business Card

logo/ name/ cell/ address/ www.Dunmere-PK.com/ space for a QR code

Requirements
Must have
• maybe a QR code (do not make prominent I may not use the QR so design where it can be taken out) that link to more about us/ landing page. needs to be modern but clean
Should not have
• clip art or script

```html
<!DOCTYPE html>
<html lang="en">
<head>
<meta charset="utf-8">
<title>Dunmere Living – Business Card</title>
<link rel="stylesheet" href="https://fonts.googleapis.com/css2?family=Poppins:wght@400&family=Yellowtail&display=swap">
<style>
  :root {
    --backdrop: #353535;
    --rust: #ae5126;
    --slate: #858489;
    --paper: #ffffff;
    --rule: rgba(255,255,255,0.55);
  }
  * { margin: 0; padding: 0; box-sizing: border-box; }
  html, body {
    width: 1200px; height: 1200px; overflow: hidden;
    background: var(--backdrop);
    font-family: "Poppins", sans-serif;
  }
  .card {
    position: absolute; top: 303px; height: 593px; overflow: hidden;
    box-shadow: 3px 3px 4px rgba(0,0,0,0.45);
  }
  .card-front { left: 201px; width: 369px; background: var(--rust); }
  .card-back  { left: 599px; width: 364px; background: var(--paper); }
  .card-bg { position: absolute; inset: 0; width: 100%; height: 100%; }

  .wordmark {
    position: absolute; left: 0; right: 0; text-align: center;
    font-weight: 400; line-height: 1;
  }
  .wordmark-name { display: block; font-size: 44px; letter-spacing: 2px; }
  .wordmark-sub  { display: block; font-size: 15px; letter-spacing: 11px; margin-top: 8px; padding-left: 11px; }
  .card-front .wordmark { top: 468px; color: var(--paper); }
  .card-back .wordmark  { top: 80px;  color: var(--rust); }

  .line { position: absolute; left: 0; right: 0; text-align: center; color: var(--paper); white-space: nowrap; }
  .person-name { top: 326px; font-family: "Yellowtail", cursive; font-size: 30px; line-height: 34px; }
  .person-title { top: 362px; font-size: 16px; line-height: 20px; letter-spacing: 0.3px; }
  .contact { font-size: 16.5px; line-height: 21px; }
  .contact-phone { top: 428px; }
  .contact-email { top: 449px; }
  .contact-web   { top: 469px; }
  .address { font-size: 16.5px; line-height: 21px; }
  .address-1 { top: 520px; }
  .address-2 { top: 541px; }

  .icon-row {
    position: absolute; top: 396px; left: 87px; width: 191px; height: 25px;
    display: flex; align-items: center; justify-content: space-between;
  }
  .icon-row .rule { flex: 1; height: 1px; background: var(--rule); }
  .icon-set { display: flex; gap: 5px; margin: 0 5px; }
  .icon-box {
    width: 25px; height: 25px; background: var(--paper); border-radius: 3px;
    display: flex; align-items: center; justify-content: center;
  }
  .icon-box svg { width: 16px; height: 16px; }
  .divider { position: absolute; top: 507px; left: 88px; width: 195px; height: 1px; background: var(--rule); }
</style>
</head>
<body>

<section class="card card-front" aria-label="Card front">
  <svg class="card-bg" viewBox="0 0 369 593" preserveAspectRatio="none" aria-hidden="true">
    <path fill="#858489" d="M0,0 H369 V425 C330,445 290,455 250,448 C180,436 120,380 60,395 C35,401 15,392 0,380 Z"/>
  </svg>
  <div class="wordmark">
    <span class="wordmark-name">DUNMERE</span>
    <span class="wordmark-sub">LIVING</span>
  </div>
</section>

<section class="card card-back" aria-label="Card back">
  <svg class="card-bg" viewBox="0 0 364 593" preserveAspectRatio="none" aria-hidden="true">
    <path fill="#858489" d="M0,294 C22,314 60,320 100,304 L364,157 V593 H0 Z"/>
    <path fill="#ae5126" d="M0,304 C26,323 64,326 104,314 L364,172 V593 H0 Z"/>
  </svg>
  <div class="wordmark">
    <span class="wordmark-name">DUNMERE</span>
    <span class="wordmark-sub">LIVING</span>
  </div>

  <div class="line person-name">Marcus Ellery</div>
  <div class="line person-title">MANAGING DIRECTOR</div>

  <div class="icon-row">
    <span class="rule"></span>
    <div class="icon-set">
      <span class="icon-box" aria-label="Phone">
        <svg viewBox="0 0 16 16"><path fill="#ae5126" d="M2,6 C2,3 14,3 14,6 L14,7.5 L11,7.5 L11,6 L5,6 L5,7.5 L2,7.5 Z M4,8 H12 L13,13 H3 Z"/></svg>
      </span>
      <span class="icon-box" aria-label="Email">
        <svg viewBox="0 0 16 16"><rect x="1.5" y="3.5" width="13" height="9" fill="#ae5126"/><path d="M2,4 L8,9 L14,4 M2,12 L6.5,7.8 M14,12 L9.5,7.8" stroke="#fff" stroke-width="1" fill="none"/></svg>
      </span>
      <span class="icon-box" aria-label="Website">
        <svg viewBox="0 0 16 16"><circle cx="8" cy="8" r="6.5" fill="#ae5126"/><path d="M5,4.5 C7,5 7,7 5.5,8 C5,9 6.5,10 6,11.5 M10,4 C9,6 11.5,6.5 12.5,7.5 M9.5,10 C10.5,10.5 11,12 10,13" stroke="#fff" stroke-width="1.1" fill="none"/></svg>
      </span>
    </div>
    <span class="rule"></span>
  </div>

  <div class="line contact contact-phone">044-987 654 321</div>
  <div class="line contact contact-email">hello@dunmere-pk.com</div>
  <div class="line contact contact-web">www.Dunmere-PK.com</div>

  <div class="divider"></div>

  <div class="line address address-1">421, Address line goes here</div>
  <div class="line address address-2">45452,Country Name</div>
</section>

</body>
</html>
```